Request for Business Card Design

Hi. My name is Marlene, I am looking for a new business card design for my company, Quarrow Signal Instruments, LLC. I really like the design you did for Tarsel Venture and was hoping you could do something similar using our full logo and our mark. I am also open to any raised texture design using our mark. I have attached our full logo, which would need to be somewhere on the card, as well as the mark in both outline and full form, as well as our brand colors / guide. The card does not have to be white, as long as our logo and mark appear. I actually like darker colored business cards more, but am open to all options. If you are interested in working with me, please let me know. We would also take the business card design into letterhead design if you can do that.

```html
<!DOCTYPE html>
<html lang="en">
<head>
<meta charset="utf-8">
<title>Quarrow Signal Instruments — Business Card</title>
<link href="https://fonts.googleapis.com/css2?family=Josefin+Sans:wght@400;600;700&display=swap" rel="stylesheet">
<style>
  :root {
    --bg: #e4e5e7;
    --brand-blue: #1a9ac0;
    --card-black: #0a0a0a;
    --ink-white: #ffffff;
    --ink-soft: #e8e8e8;
  }
  * { margin: 0; padding: 0; box-sizing: border-box; }
  html, body {
    width: 1200px; height: 800px; overflow: hidden;
    background: var(--bg);
    font-family: "Josefin Sans", sans-serif;
  }
  .canvas {
    width: 1200px; height: 800px;
    display: flex; align-items: center; justify-content: center; gap: 40px;
  }
  .card {
    position: relative;
    width: 540px; height: 309px;
    box-shadow: 0 6px 18px rgba(0,0,0,0.18);
    overflow: hidden;
  }
  .card-front { background: var(--brand-blue); }
  .card-back { background: var(--card-black); color: var(--ink-white); }

  .brand {
    display: flex; align-items: center; gap: 14px;
    color: var(--ink-white);
  }
  .brand-dot {
    width: 46px; height: 46px; border-radius: 50%;
    background: var(--ink-white); flex: none;
  }
  .brand-name {
    font-weight: 700; font-size: 26px; line-height: 1.05;
    text-transform: uppercase; letter-spacing: 0.06em;
  }
  .card-front .brand {
    position: absolute; left: 50%; top: 50%;
    transform: translate(-50%, -50%);
  }
  .card-back .brand {
    position: absolute; right: 34px; top: 34px;
  }
  .card-back .brand-dot { background: var(--brand-blue); width: 38px; height: 38px; }
  .card-back .brand-name { font-size: 21px; }

  .person { position: absolute; left: 34px; top: 118px; }
  .person-name {
    color: var(--brand-blue); font-weight: 700; font-size: 17px;
    text-transform: uppercase; letter-spacing: 0.02em;
  }
  .person-title { font-size: 13px; margin-top: 3px; color: var(--ink-soft); }

  .accent-rule {
    position: absolute; left: 250px; right: 34px; top: 130px;
    height: 1px; background: var(--brand-blue);
  }

  .contact-list {
    position: absolute; left: 34px; top: 170px;
    list-style: none; font-size: 12.5px; line-height: 1.65; color: var(--ink-soft);
  }
  .contact-list li { display: flex; align-items: center; gap: 8px; }
  .contact-list svg { width: 12px; height: 12px; flex: none; }

  .address {
    position: absolute; right: 34px; bottom: 34px;
    padding-left: 14px; border-left: 1px solid var(--brand-blue);
    font-size: 13px; line-height: 1.55; color: var(--ink-soft);
  }
</style>
</head>
<body>
<main class="canvas">
  <section class="card card-front" aria-label="Card front">
    <div class="brand">
      <span class="brand-dot"></span>
      <span class="brand-name">Quarrow Signal<br>Instruments</span>
    </div>
  </section>

  <section class="card card-back" aria-label="Card back">
    <div class="brand">
      <span class="brand-dot"></span>
      <span class="brand-name">Quarrow Signal<br>Instruments</span>
    </div>

    <div class="person">
      <p class="person-name">Dr. Elias Harwood</p>
      <p class="person-title">President &amp; CEO</p>
    </div>
    <div class="accent-rule"></div>

    <ul class="contact-list">
      <li>
        <svg viewBox="0 0 12 12" fill="none" stroke="#1a9ac0" stroke-width="1.4"><path d="M2 1.5h2.2l.9 2.5-1.3.9a6 6 0 0 0 3.3 3.3l.9-1.3 2.5.9v2.2A1 1 0 0 1 9.5 11 8.5 8.5 0 0 1 1 2.5a1 1 0 0 1 1-1z"/></svg>
        +001 555 210 4418
      </li>
      <li>
        <svg viewBox="0 0 12 12" fill="none" stroke="#1a9ac0" stroke-width="1.3"><rect x="3" y="1" width="6" height="3"/><rect x="1" y="4" width="10" height="5"/><rect x="3" y="7.5" width="6" height="3.5"/></svg>
        +001 555 210 4490
      </li>
      <li>
        <svg viewBox="0 0 12 12" fill="none" stroke="#1a9ac0" stroke-width="1.3"><rect x="1" y="2.5" width="10" height="7"/><path d="M1 2.5l5 4 5-4"/></svg>
        info@quarrowsignal.com
      </li>
      <li>
        <svg viewBox="0 0 12 12" fill="none" stroke="#1a9ac0" stroke-width="1.2"><circle cx="6" cy="6" r="5"/><ellipse cx="6" cy="6" rx="2.2" ry="5"/><path d="M1 6h10"/></svg>
        www.quarrowsignal.com
      </li>
    </ul>

    <p class="address">1180 Fieldstone Parkway<br>Aldermoor, CO 80990</p>
  </section>
</main>
</body>
</html>
```